Silver Wren Nectar Label Design

I need to design a label for my honey

Silver Wren Nectar - 100% Raw Natural Australian Honey from Flowerdale Victoria

I like clean uncluttered designs - ideally with a hexagon background to tie into the hive - not garish or too brightly coloured, classic to the point of being understated.
Would like the label to be a wrap around for our 500G jars

Label size is

face - 4CM
Height 6.5CM
Wrap around dimension 16 CM (corners are rounded)

Would like to include the "produce of Australia Logo on the side - image here https://www.labelregistry-example.org/files/originmarkjpg

Possibly some text on one of the sides also along the lines of

Natures gold from the Shire of Murrindindi. Our bees live and work in the beautiful countryside of Flowerdale, Victoria. We are an independent 100% Australian owned honey producer. our honey is made as nature intended, nothing added, taken away or blended with it, just pure raw natural honey. for more information or enquiries please drop us a line at silverwrennectar@mailbox-example.net

Our hives are in the countryside in Flowerdale and there are lots of parrots, Lorikeets and Cockatoos - the king parrots are particularly prevalent and we would very much like them to feature in the logo and be prominent in the label design

if it helps or you are looking for images of bees - I am a photographer and have some images of bees - are than happy to provide these in whatever formate works - here are some of my images https://www.photohub-example.com/member/Tmorrowshots

Target Market(s)

People looking to purchase pure Australian honey, unadulterated and guaranteed 100% natural

Logo Text

Silver Wren Nectar, ( natures gold from Flowerdale) optional

Font styles to use
Decorative

Colors

Designer to choose colors to be used in the design.

Requirements
Must have
• A silver wren image (male green and red)
• uncluttered and clean image
• connection to nature and natural products
• Australian owned and produced
• Natural product
• Independent, Victorian ethical honey producer
• must look and feel all local business
• Sorry should have stated that the jars are 500gms, they will contain 500 grams of Honey
• Please see guidance for honey labelling
• https://brindlecreekapiary-example.com.au/honey-labelling/
• regarding the nutritional content, we will need to include this
• I would also like to have a small section "Packed __/__/__ Batch____" to allow me to then insert a date in order to track product
• Silver Wren Nectar
• 1184 Tarrock-Benning Road. Flowerdale. Victoria. 3717
Nice to have
• Hexagon background design to tie it to the bees
• Calorific content of honey, this can be found on the web easy enough
• I like the idea/concept of a gauge on the side of one of the side panels that shows people how much honey they have left and of course when it gets down to the bottom of the label suggests they get some more before they run out
Should not have
• lots of clashing vibrant colours - need to be classically understated and clean
• Must not be corporate, big business

```html
<!DOCTYPE html>
<html lang="en">
<head>
<meta charset="utf-8">
<title>Silver Wren Nectar – Jar Label</title>
<link href="https://fonts.googleapis.com/css2?family=Kanit:wght@300;400;500;600;700&display=swap" rel="stylesheet">
<style>
  :root{
    --page:#ffffff;
    --label-rim:#fdf1b4;
    --label:#fcd94c;
    --front:#fdf5b6;
    --front-deep:#fbe97a;
    --brown:#6b1208;
    --orange:#f7941d;
    --orange-deep:#e06a10;
    --red:#ff1a1a;
    --packed:#fbbe36;
    --leaf:#2aa52a;
    --art-gold:#e6a52e;
    --art-red:#e8332a;
  }
  *{margin:0;padding:0;box-sizing:border-box;}
  html,body{width:1200px;height:1000px;overflow:hidden;background:var(--page);}
  body{font-family:"Kanit",sans-serif;color:var(--brown);position:relative;}
  .abs{position:absolute;}

  .label-rim{left:7px;top:233px;width:1186px;height:498px;border-radius:52px;background:var(--label-rim);}
  .label{left:21px;top:247px;width:1157px;height:470px;border-radius:40px;background:var(--label);overflow:hidden;}

  /* side quotes */
  .quote{left:9px;font-size:10px;font-weight:500;line-height:18px;width:130px;white-space:nowrap;}
  .quote span{display:block;padding-left:9px;}
  .quote .hl{color:#fff;border-radius:0 9px 9px 0;width:111px;}
  .hl.orange{background:var(--orange);}
  .hl.deep{background:var(--orange-deep);}
  .hl.red{background:var(--red);}

  /* front panel */
  .front{left:147px;top:0;width:323px;height:470px;
    background:radial-gradient(circle at 50% 45%, var(--front) 0%, #fefac8 55%, var(--front-deep) 100%);}
  .brand{left:0;width:323px;top:44px;text-align:center;font-weight:700;color:var(--brown);white-space:nowrap;}
  .brand-top{display:block;font-size:29px;line-height:32px;letter-spacing:0.3px;}
  .brand-main{display:block;font-size:58px;line-height:60px;letter-spacing:-0.5px;}
  .rule{left:31px;top:145px;width:260px;height:1px;background:var(--brown);}
  .tagline{left:0;width:323px;top:153px;text-align:center;font-size:15px;font-weight:300;line-height:19px;white-space:nowrap;}
  .artwork{left:88px;top:216px;width:168px;height:140px;border-radius:28px;
    background:linear-gradient(160deg,var(--art-gold) 0%,#d98f25 55%,var(--art-red) 100%);}
  .badge-natural{left:19px;top:376px;width:74px;height:48px;border-radius:8px;background:var(--leaf);}
  .badge-origin{left:117px;top:390px;width:88px;height:34px;border:2px solid var(--leaf);background:#fff;}
  .weight{left:230px;top:386px;font-size:31px;font-weight:700;line-height:38px;white-space:nowrap;}

  /* info panel */
  .story{left:523px;top:30px;width:581px;font-size:15px;font-weight:300;line-height:18px;text-align:justify;}
  .story b{font-weight:600;}

  .nutrition{left:530px;top:127px;width:269px;}
  .nutrition .bar{height:2px;background:var(--brown);}
  .nutrition .bar.thin{height:1px;}
  .nutrition .bar.heavy{height:3px;}
  .nutrition h2{font-size:17px;font-weight:600;text-align:center;line-height:26px;margin-top:2px;}
  .serv{font-size:11.5px;line-height:15px;padding-left:7px;display:grid;grid-template-columns:130px auto;margin-bottom:6px;}
  .heads{display:grid;grid-template-columns:126px 72px 70px;font-size:10.5px;line-height:12px;padding:4px 0 3px;}
  .rows{padding:3px 0 4px;}
  .row{display:grid;grid-template-columns:126px 44px 26px 44px 29px;font-size:11.5px;line-height:20px;}
  .row .n{text-align:right;padding-right:6px;}
  .row .name{padding-left:9px;}
  .footnote{font-size:10.5px;line-height:14px;margin-top:4px;padding-left:3px;}

  .details{left:827px;top:130px;width:310px;font-size:15px;font-weight:300;line-height:18.5px;}
  .details h3{font-size:15px;font-weight:600;line-height:18.5px;}
  .details p{margin-bottom:18px;white-space:nowrap;}
  .details .address{font-weight:600;margin-bottom:18px;}

  .packed{left:827px;top:385px;width:230px;height:53px;border-radius:14px;background:var(--packed);
    font-size:12px;font-weight:600;line-height:15px;padding:10px 0 0 19px;}
  .packed .line{display:grid;grid-template-columns:60px 47px 47px 20px;}

  /* dimension marks */
  .dim{height:2px;background:var(--brown);}
  .dim::before,.dim::after{content:"";position:absolute;top:-9px;width:2px;height:20px;background:var(--brown);}
  .dim::before{left:0;} .dim::after{right:0;}
  .dim-text{font-size:24px;font-weight:400;text-align:center;line-height:30px;}
</style>
</head>
<body>
  <div class="abs label-rim"></div>
  <div class="abs label">
    <div class="abs quote" style="top:52px;">
      <span>“My Son,</span>
      <span class="hl orange">eat thou honey,</span>
      <span>for it is good”</span>
    </div>
    <div class="abs quote" style="top:209px;">
      <span>“Yeah, you have</span>
      <span class="hl deep">done a great thing,</span>
      <span>keep up the good”</span>
    </div>
    <div class="abs quote" style="top:347px;">
      <span>“You’re amazing, keep</span>
      <span>going and remember:</span>
      <span class="hl red">To be prepared</span>
      <span>is a half the victory”</span>
    </div>

    <section class="abs front">
      <h1 class="abs brand"><span class="brand-top">SILVER WREN</span><span class="brand-main">NECTAR</span></h1>
      <div class="abs rule"></div>
      <p class="abs tagline">100% Raw Natural Australian Honey<br>from Flowerdale Victoria</p>
      <div class="abs artwork" role="img" aria-label="Illustration of a red and green wren perched on crossed honey dippers over a gold hexagon"></div>
      <div class="abs badge-natural" role="img" aria-label="Natural product badge"></div>
      <div class="abs badge-origin" role="img" aria-label="Country of origin badge"></div>
      <div class="abs weight">500 g</div>
    </section>

    <p class="abs story"><b>Natures gold</b> from the Shire of Murrindindi. Our bees live and work in the beautiful countryside of Flowerdale, Victoria. We are an independent 100% Australian owned honey producer. Our honey is made as nature intended, nothing added, taken away or blended with it, just pure raw natural honey.</p>

    <div class="abs nutrition">
      <div class="bar"></div>
      <h2>Nutrition Information</h2>
      <div class="serv"><span>Servings per package :</span><span>50.00</span><span>Serving size :</span><span>20.00 g</span></div>
      <div class="bar"></div>
      <div class="heads"><span></span><span>Average Quantity per Serving</span><span>Average Quantity per 100 g</span></div>
      <div class="bar thin"></div>
      <div class="rows">
        <div class="row"><span class="name">Energy</span><span class="n">280</span><span>kJ</span><span class="n">1400</span><span>kJ</span></div>
        <div class="row"><span class="name">Protein</span><span class="n">0.0</span><span>g</span><span class="n">0.2</span><span>g</span></div>
        <div class="row"><span class="name">Fat total</span><span class="n">0.0</span><span>g</span><span class="n">0.0</span><span>g</span></div>
        <div class="row"><span class="name">- saturated</span><span class="n">0.0</span><span>g</span><span class="n">0.0</span><span>g</span></div>
        <div class="row"><span class="name">Carbohydrate</span><span class="n">16.4</span><span>g</span><span class="n">82.1</span><span>g</span></div>
        <div class="row"><span class="name">- sugars</span><span class="n">16.4</span><span>g</span><span class="n">82.1</span><span>g</span></div>
        <div class="row"><span class="name">Sodium</span><span class="n">3</span><span>mg</span><span class="n">14</span><span>mg</span></div>
      </div>
      <div class="bar heavy"></div>
      <p class="footnote">* Sugars naturally occurring in honey</p>
    </div>

    <div class="abs details">
      <h3>Ingredients :</h3>
      <p>100% Natural Australian Honey</p>
      <h3>Storage Instructions :</h3>
      <p>Store in a cool, dry place</p>
      <h3 class="address">1184 Tarrock-Benning Road. Flowerdale.<br>Victoria. 3717<br>Australia</h3>
      <h3>For more information or enquiries<br>please drop us a line at :</h3>
      <p>silverwrennectar@mailbox-example.net</p>
    </div>

    <div class="abs packed">
      <div class="line"><span>Packed</span><span>:</span><span>/</span><span>/</span></div>
      <div class="line"><span>Batch</span><span>:</span></div>
    </div>
  </div>

  <div class="abs dim" style="left:169px;top:749px;width:322px;"></div>
  <div class="abs dim-text" style="left:169px;top:757px;width:322px;">4.5 cm</div>
  <div class="abs dim" style="left:22px;top:805px;width:1155px;"></div>
  <div class="abs dim-text" style="left:22px;top:807px;width:1155px;">16 cm</div>
</body>
</html>
```